Heron Loan Partners Business Card

We need a business card design for our mortgage servicing company. In addition to servicing the loans of homeowners, we help homeowners with purchasing their homes and any mortgage refinancing. We would like to see designs that use the colors in the logo attached below (gold-ish yellow and navy blue), and any other design you deem fit! The design should communicate a simpler life with smart mortgages provided by Heron.

```html
<!DOCTYPE html>
<html lang="en">
<head>
<meta charset="utf-8">
<title>Heron Loan Partners Business Card</title>
<link href="https://fonts.googleapis.com/css2?family=Open+Sans:wght@400;600;700&display=swap" rel="stylesheet">
<style>
  :root {
    --page: #ecebe7;
    --card-dark: #1f1f23;
    --emboss: #2b2b31;
    --gold: #dfb540;
    --navy: #1c1f5e;
    --text-light: #e9e9ec;
  }
  * { margin: 0; padding: 0; box-sizing: border-box; }
  html, body { width: 1200px; height: 780px; overflow: hidden; }
  body {
    background: var(--page);
    font-family: "Open Sans", sans-serif;
    position: relative;
  }
  .card {
    position: absolute;
    border-radius: 4px;
    box-shadow: 0 10px 24px rgba(0,0,0,0.18);
    overflow: hidden;
  }
  /* Back side: portrait, dark */
  .card-back {
    left: 130px; top: 110px;
    width: 330px; height: 560px;
    background: var(--card-dark);
  }
  .back-brand {
    position: absolute;
    left: 30px; top: 40px;
    font-weight: 700;
    font-size: 26px;
    line-height: 1.1;
    color: var(--emboss);
  }
  .back-details {
    position: absolute;
    right: 40px; bottom: 46px;
    text-align: right;
    color: var(--text-light);
    font-size: 14px;
    line-height: 1.55;
  }
  .person-name {
    color: var(--gold);
    font-weight: 700;
    font-size: 28px;
    line-height: 1.15;
  }
  .person-role { font-size: 15px; margin-bottom: 10px; }
  .address { margin-bottom: 12px; }
  .contact-line {
    display: flex; justify-content: flex-end; align-items: center; gap: 8px;
  }
  .contact-line svg { width: 14px; height: 14px; flex: none; }
  .edge-tab {
    position: absolute;
    right: 0; bottom: 250px;
    width: 22px; height: 56px;
    background: var(--gold);
  }
  /* Front side: landscape, gold */
  .card-front {
    left: 540px; top: 200px;
    width: 560px; height: 320px;
    background: var(--gold);
    display: flex; align-items: center; justify-content: center;
  }
  .front-brand {
    display: flex; align-items: center; gap: 14px;
    color: var(--navy);
    font-weight: 700;
    font-size: 38px;
  }
  .brand-mark {
    width: 22px; height: 22px;
    border-radius: 50%;
    background: var(--navy);
  }
</style>
</head>
<body>
  <section class="card card-back">
    <div class="back-brand">Heron<br>Loan Partners</div>
    <div class="edge-tab"></div>
    <div class="back-details">
      <div class="person-name">Delia Marsh</div>
      <div class="person-role">Co-Founder</div>
      <div class="address">418 Lakeside Ave. Suite 300<br>Brookfield, TX 75210</div>
      <div class="contact-line">(555) 214-6830
        <svg viewBox="0 0 24 24"><path fill="#dfb540" d="M6.6 10.8a15 15 0 0 0 6.6 6.6l2.2-2.2a1 1 0 0 1 1-.25 11.4 11.4 0 0 0 3.6.57 1 1 0 0 1 1 1V20a1 1 0 0 1-1 1A17 17 0 0 1 3 4a1 1 0 0 1 1-1h3.5a1 1 0 0 1 1 1c0 1.25.2 2.45.57 3.57a1 1 0 0 1-.25 1z"/></svg>
      </div>
      <div class="contact-line">info@website.com
        <svg viewBox="0 0 24 24"><rect x="2" y="5" width="20" height="14" rx="2" fill="#dfb540"/><path d="M3 6l9 7 9-7" stroke="#1f1f23" stroke-width="2" fill="none"/></svg>
      </div>
      <div class="contact-line">www.website.com
        <svg viewBox="0 0 24 24"><circle cx="12" cy="12" r="10" fill="#dfb540"/><path d="M2 12h20M12 2c3 3 3 17 0 20M12 2c-3 3-3 17 0 20" stroke="#1f1f23" stroke-width="1.5" fill="none"/></svg>
      </div>
    </div>
  </section>

  <section class="card card-front">
    <div class="front-brand"><span class="brand-mark"></span>Heron Loan Partners</div>
  </section>
</body>
</html>
```